Bellmere Home Inspection Needs an Eye Catching FLYER

We need a EYE CATCHING flyer that will be sent to thousands of realtors. Our Riverside/San Bernardino County Inspection company performs residential/light commercial inspections for potential home buyers. We hope the flyer can highlight the services performed and present a professional look for the company. The final design should leave realtors thinking Bellmere Home Inspections is the #1 inspection company in the area.

Target Market(s)

Realtors, Home Buyers, Home Sellers, and Home Owners.

Industry/Entity Type

Home Inspection

Font styles to use
Sans Serif

Colors
0392cd
33a6d7
3276b5
eaeaea
000000
ffffff

Requirements
Must have
• Must have a list of services Provided:
• Exterior, Interior, Electrical, Plumbing, Roof, Heating/Air cooling, Structural, Appliances, and Mold/Dry Rot.
• Tag Line "We inspect homes like we're buying them ourselves."
• number: 951-284-6193 Domain: bellmerechecks.com ,Email: owen@bellmerechecks.com
Nice to have
• Let realtors know we follow National Guild of Property Examiners (NGPE) Standards of Practice (SoP)
• Veteran Owned and Operated
• Discounts from the flyer of 20%
• Discounts to all veterans and public service members.

```html
<!DOCTYPE html>
<html lang="en">
<head>
<meta charset="utf-8">
<title>Bellmere Home Inspections Flyer</title>
<link rel="stylesheet" href="https://fonts.googleapis.com/css2?family=Oswald:wght@300;600&family=Poppins:wght@400;500;600;700&family=Roboto:wght@400;700&family=Lobster&display=swap">
<style>
  :root {
    --brand-blue: #146f99;
    --brand-blue-deep: #0f6690;
    --panel-blue: rgba(14, 104, 148, 0.93);
    --ink: #111111;
    --text: #2b2b2b;
    --band-grey: #f3f3f3;
    --white: #ffffff;
    --stage: #e6e6e6;
  }
  * { margin: 0; padding: 0; box-sizing: border-box; }
  html, body { width: 1200px; height: 1200px; overflow: hidden; background: var(--stage); }
  .flyer {
    position: absolute; left: 190px; top: 20px;
    width: 820px; height: 1160px;
    background: var(--white);
    overflow: hidden;
    font-family: "Roboto", sans-serif;
    color: var(--text);
  }
  .hero-photo {
    position: absolute; left: 0; top: 32px; width: 820px; height: 347px;
    background: linear-gradient(160deg, #cfe2ef 0%, #8fa79a 35%, #6f8f55 60%, #c87aa2 80%, #5f9a3c 100%);
  }
  .headline-panel {
    position: absolute; left: 498px; top: 32px; width: 297px; height: 347px;
    background: var(--panel-blue);
    padding: 66px 0 0 32px;
    color: var(--white);
    font-family: "Oswald", sans-serif;
    text-transform: uppercase;
    white-space: nowrap;
  }
  .headline-panel .lead { font-weight: 300; font-size: 38px; line-height: 46px; letter-spacing: -0.8px; }
  .headline-panel .focus { font-weight: 600; font-size: 47px; line-height: 62px; margin-top: 2px; letter-spacing: -1px; }
  .intro-band {
    position: absolute; left: 0; top: 469px; width: 820px; height: 203px;
    background: var(--band-grey);
  }
  .tagline {
    position: absolute; left: 58px; top: 415px; width: 420px;
    font-family: "Roboto", sans-serif; font-weight: 700; font-size: 17px; line-height: 23px;
    color: var(--ink); text-transform: uppercase;
  }
  .intro-copy {
    position: absolute; left: 58px; top: 481px;
    font-size: 14px; line-height: 18px; color: var(--ink);
  }
  .intro-copy p { margin-bottom: 18px; width: 436px; text-align: justify; }
  .intro-copy p.wide { width: 705px; margin-top: -12px; text-align: left; }
  .brand-seal {
    position: absolute; left: 525px; top: 364px; width: 234px; height: 234px;
    border-radius: 50%;
    background: var(--white);
    border: 5px solid var(--brand-blue);
    box-shadow: 0 0 0 8px var(--white);
    display: flex; flex-direction: column; align-items: center; justify-content: center;
    text-align: center;
    font-family: "Poppins", sans-serif; font-weight: 600; color: var(--brand-blue);
  }
  .brand-seal .name { font-size: 40px; line-height: 44px; }
  .brand-seal .sub { font-size: 15px; line-height: 20px; }
  .services-label {
    position: absolute; left: 54px; top: 721px; width: 234px; height: 56px;
    border-radius: 28px; background: var(--brand-blue-deep);
    color: var(--white); font-family: "Lobster", cursive; font-size: 36px;
    display: flex; align-items: center; justify-content: center; padding-right: 30px;
  }
  .service { position: absolute; width: 230px; }
  .service h3 {
    display: flex; align-items: center; gap: 10px;
    font-family: "Poppins", sans-serif; font-weight: 500; font-size: 24px; line-height: 30px;
    color: var(--brand-blue);
  }
  .service .num {
    width: 22px; height: 22px; border-radius: 50%; background: var(--ink); color: var(--white);
    font-size: 13px; font-weight: 700; display: flex; align-items: center; justify-content: center;
    flex: none;
  }
  .service p {
    margin: 6px 0 0 7px; width: 212px; font-family: "Poppins", sans-serif; font-size: 13px; line-height: 16.5px; color: #333;
  }
  .footer-band {
    position: absolute; left: 0; top: 1066px; width: 820px; height: 94px; background: var(--ink);
  }
  .contact-lines {
    position: absolute; left: 72px; top: 1084px;
    font-family: "Poppins", sans-serif; font-size: 22px; line-height: 27px; color: var(--white);
  }
  .phone-pill {
    position: absolute; left: 487px; top: 1069px; width: 340px; height: 84px;
    background: var(--brand-blue-deep);
    border: 3px solid var(--white); border-right: none;
    border-radius: 30px 0 0 30px;
    display: flex; align-items: center; padding-left: 22px;
    font-family: "Poppins", sans-serif; font-weight: 700; font-size: 37px; color: var(--white);
    letter-spacing: 0.5px;
  }
</style>
</head>
<body>
  <main class="flyer">
    <div class="hero-photo" role="img" aria-label="Photo of a large suburban house with flowering shrubs, framed by a magnifying glass"></div>
    <div class="headline-panel">
      <div class="lead">Are you ready<br>to schedule</div>
      <div class="focus">A Home<br>Inspection?</div>
    </div>

    <div class="intro-band"></div>
    <h2 class="tagline">We inspect homes like we’re<br>buying them ourselves!</h2>
    <div class="intro-copy">
      <p>From the attic to the crawlspace, we are equipped to inspect the whole home and property.</p>
      <p>At Bellmere Home Inspections we inspect every part of your property. From the very first step on the property our experts are inspecting everything from the exterior, interior, roof, plumbing, electrical, structural and ventilation.</p>
      <p class="wide">At Bellmere we go the extra step to make sure our clients are making the smartest and safest decision when buying a new home. Call us today to schedule a full service Home Inspection.</p>
    </div>

    <div class="brand-seal">
      <span class="name">Bellmere</span>
      <span class="sub">Home Inspections</span>
    </div>

    <div class="services-label">Services</div>

    <section class="service" style="left:68px; top:808px;">
      <h3><span class="num">1</span>Exterior</h3>
      <p>Walls, siding, patios, decks, walkways, garage door, exterior fixtures and outlets, windows</p>
    </section>
    <section class="service" style="left:322px; top:808px;">
      <h3><span class="num">2</span>Structure</h3>
      <p>Foundation, framing, roof , walls, sill plate, landscape swale, crawlspace and attic</p>
    </section>
    <section class="service" style="left:560px; top:808px;">
      <h3><span class="num">3</span>Roof</h3>
      <p>Eaves, gutters, downspouts, vents, chimneys and all vent stacks</p>
    </section>
    <section class="service" style="left:68px; top:914px;">
      <h3><span class="num">4</span>Interior</h3>
      <p>Walls, floors, drywall, attic space, finishes, windows, doors and doors</p>
    </section>
    <section class="service" style="left:322px; top:914px;">
      <h3><span class="num">5</span>Electrical</h3>
      <p>Outlets, light fixtures, switches, main panel, service entrance conductors</p>
    </section>
    <section class="service" style="left:560px; top:914px;">
      <h3><span class="num">6</span>Appliances</h3>
      <p>Dishwasher, ranges, refrigerators, waste disposal, laundry facilities, microwave</p>
    </section>

    <div class="footer-band"></div>
    <div class="contact-lines">
      <div>owen@bellmerechecks.com</div>
      <div>www.bellmerechecks.com</div>
    </div>
    <div class="phone-pill">951-284-6193</div>
  </main>
</body>
</html>
```